Business Card Design Project

We need a Business Card for an Mechanical Engineering firm in Singapore. The design should be Modern & Technical looking, yet eye catching.

Our company deals in Cutting Tools & Machine Accessories for the Manufacturing Industries such as Oil & Gas, Aero Space, etc... For more information on our Company, you can either email me or view our website www.torvalen.com.sg.

We are trying to revamp our image to give our consumers a fresh new perspective to our company, so we welcome all ideas.

Industry/Entity Type

Business

Requirements
Must have
• Must incorporate New Company Logo into the card as shown in Uploaded file.

```html
<!DOCTYPE html>
<html lang="en">
<head>
<meta charset="utf-8">
<title>Torvalen Tools – Business Card</title>
<link rel="stylesheet" href="https://fonts.googleapis.com/css2?family=Oswald:wght@400&family=Open+Sans:wght@400&family=Noto+Serif:wght@700&display=swap">
<style>
  :root {
    --backdrop: #e4e4e4;
    --card-dark: #221c1c;
    --card-light: #ffffff;
    --brand-red: #a8161c;
    --brand-ink: #4a2a2c;
    --text-light: #f2f2f2;
  }
  * { box-sizing: border-box; margin: 0; padding: 0; }
  html, body {
    width: 1200px;
    height: 951px;
    overflow: hidden;
    background: var(--backdrop);
  }
  .canvas {
    position: relative;
    width: 1200px;
    height: 951px;
  }
  .card {
    position: absolute;
    width: 580px;
    height: 340px;
    border-radius: 22px;
    overflow: hidden;
    box-shadow: 0 10px 24px rgba(0,0,0,0.25);
  }

  /* Back side */
  .card-back {
    left: 110px;
    top: 100px;
    background: var(--card-dark);
  }
  .card-back .edge {
    position: absolute;
    top: 0;
    bottom: 0;
    width: 20px;
    background: var(--brand-red);
  }
  .card-back .edge-left { left: 0; }
  .card-back .edge-right { right: 0; }
  .card-back .brand {
    position: absolute;
    left: 0; right: 0;
    top: 112px;
    display: flex;
    justify-content: center;
    align-items: center;
    gap: 14px;
  }
  .card-back .wordmark { color: var(--text-light); font-size: 48px; }
  .card-back .website {
    position: absolute;
    left: 0; right: 0;
    top: 232px;
    text-align: center;
    font-family: "Open Sans", sans-serif;
    font-size: 17px;
    letter-spacing: 0.5px;
    color: var(--text-light);
  }

  /* Front side */
  .card-front {
    left: 510px;
    top: 510px;
    background: var(--card-dark);
  }
  .card-front .top-panel {
    position: absolute;
    left: 0; right: 0; top: 0;
    height: 150px;
    background: linear-gradient(#ffffff, #f1f1f1);
    display: flex;
    justify-content: center;
    align-items: center;
    gap: 12px;
    padding-top: 10px;
  }
  .card-front .wordmark { color: var(--brand-ink); font-size: 38px; }
  .card-front .divider {
    position: absolute;
    left: 0; right: 0;
    top: 150px;
    height: 7px;
    background: var(--brand-red);
  }
  .card-front .contact {
    position: absolute;
    left: 0; right: 0;
    top: 180px;
    text-align: center;
    color: var(--text-light);
    font-family: "Open Sans", sans-serif;
    font-size: 14.5px;
    line-height: 1.45;
  }
  .card-front .person {
    font-family: "Noto Serif", serif;
    font-weight: 700;
    font-size: 22px;
    margin-bottom: 6px;
  }
  .card-front .contact .row span + span { margin-left: 18px; }

  .wordmark {
    font-family: "Oswald", sans-serif;
    font-weight: 400;
    letter-spacing: 1px;
    text-transform: uppercase;
    line-height: 1;
  }
  .brand-dot {
    display: block;
    border-radius: 50%;
    background: var(--brand-red);
  }
  .card-back .brand-dot { width: 30px; height: 30px; }
  .card-front .brand-dot { width: 24px; height: 24px; }
</style>
</head>
<body>
<main class="canvas">
  <section class="card card-back" aria-label="Business card, back">
    <div class="edge edge-left"></div>
    <div class="edge edge-right"></div>
    <div class="brand">
      <span class="brand-dot"></span>
      <span class="wordmark">Torvalen Tools</span>
    </div>
    <p class="website">www.torvalentools.com</p>
  </section>

  <section class="card card-front" aria-label="Business card, front">
    <div class="top-panel">
      <span class="brand-dot"></span>
      <span class="wordmark">Torvalen Tools</span>
    </div>
    <div class="divider"></div>
    <div class="contact">
      <p class="person">Marcus Lindqvist</p>
      <p class="row">Phone: 512-004-219</p>
      <p class="row"><span>info@torvalentools.com</span><span>www.torvalentools.com</span></p>
      <p class="row">4410 Harlow Crest Rd., Suite 208-115, Dalton, TX 78510</p>
    </div>
  </section>
</main>
</body>
</html>
```